4th Generation Family Business Needs a New Card Design!

We are a family owned 4th Generation company. We are based in the Sydney, Australia area and we are desperately in need of a more modern and classy card. We are monumental masons who design, supply & erect lasting memorials throughout cemeteries in Sydney. Our customers are normally in a period of grieving. I have attached logo files that will need to be implemented on the card. Company was established 1935. Australian Owned and Operated. Card needs to be designed to PIXO.com specification.

Target Market(s)

Our target market is based upon people that a grieving for family members that have passed away. We also deal with alot of companies that own and operate cemeteries.

Industry/Entity Type

Business

Contact Information for Business Card

Simon Harcourt, Operations Manager, 0417293086, simon@harcourtmemorials.com.au
Lewis Harcourt, Director, 0491630572, lewis@harcourtmemorials.com.au
Phone # 02 9561 3048
Website: www.harcourtmemorials.com.au
Address: Suite 17, 8 Palfrey Lane, West Carlow, Sydney NSW 2156

Font styles to use
Serif
Decorative
Script

Requirements
Must have
• Would like to see the logo nicely implemented with a modern design. Embossed lettering would be a nice additive.

```html
<!DOCTYPE html>
<html lang="en">
<head>
<meta charset="utf-8">
<title>Harcourt Memorials – Business Cards</title>
<link rel="stylesheet" href="https://fonts.googleapis.com/css2?family=Source+Sans+3:wght@400;600;700&display=swap">
<style>
  :root {
    --backdrop: #2b2b2b;
    --card: #141414;
    --gold: #f2b705;
    --white: #f2f2f2;
    --muted: #d6d6d6;
    --rule: #8a6a10;
  }
  * { box-sizing: border-box; margin: 0; padding: 0; }
  html, body {
    width: 1200px; height: 900px; overflow: hidden;
    background: var(--backdrop);
    font-family: "Source Sans 3", Arial, sans-serif;
  }
  .stage {
    position: relative; width: 1200px; height: 900px;
    display: flex; align-items: center; justify-content: center; gap: 40px;
  }
  .card {
    width: 540px; height: 310px;
    background: var(--card);
    border-radius: 22px;
    position: relative;
    box-shadow: 0 14px 30px rgba(0,0,0,.45);
    color: var(--white);
  }
  /* front: contacts */
  .card--front { display: flex; align-items: center; }
  .brand {
    display: flex; flex-direction: column; align-items: center; gap: 10px;
  }
  .brand__mark {
    width: 16px; height: 16px; background: var(--gold);
  }
  .brand__name {
    font-weight: 600; color: var(--white);
    text-transform: uppercase; letter-spacing: 2px; text-align: center;
    line-height: 1.15;
  }
  .card--front .brand { width: 240px; }
  .card--front .brand__name { font-size: 26px; }
  .divider {
    width: 1px; height: 210px;
    background: linear-gradient(to bottom, transparent, var(--rule) 15%, var(--rule) 85%, transparent);
  }
  .contacts { padding-left: 24px; display: flex; flex-direction: column; gap: 18px; }
  .person__name { color: var(--gold); font-weight: 700; font-size: 17px; }
  .person__role { color: var(--muted); font-size: 13.5px; margin-bottom: 4px; }
  .person__line { display: flex; align-items: center; gap: 7px; font-size: 13.5px; color: var(--white); line-height: 1.45; }
  .icon { width: 11px; height: 11px; flex: none; }
  /* back: company */
  .card--back {
    display: flex; flex-direction: column; align-items: center; justify-content: center;
  }
  .card--back .brand__name { font-size: 30px; }
  .company-info { margin-top: 34px; text-align: center; font-size: 13.5px; line-height: 1.7; }
  .company-info .label { color: var(--gold); font-weight: 600; }
  .company-info .sep { color: var(--muted); margin: 0 10px; }
  .company-info .web { color: var(--gold); }
</style>
</head>
<body>
<main class="stage">
  <section class="card card--front">
    <div class="brand">
      <span class="brand__mark"></span>
      <span class="brand__name">Harcourt<br>Memorials</span>
    </div>
    <div class="divider"></div>
    <div class="contacts">
      <div class="person">
        <p class="person__name">Simon Harcourt</p>
        <p class="person__role">Operations Manager</p>
        <p class="person__line">
          <svg class="icon" viewBox="0 0 12 12"><path fill="#f2b705" d="M2.4 1l2 2.2-1 1.2c.7 1.5 1.8 2.6 3.3 3.3l1.2-1 2.1 2-1.1 1.8C5.4 10.2 1.8 6.6 1 3l1.4-2z"/></svg>
          0417293086
        </p>
        <p class="person__line">
          <svg class="icon" viewBox="0 0 12 12"><rect x="1" y="2.5" width="10" height="7" fill="#f2b705"/><path d="M1 2.5l5 4 5-4" fill="none" stroke="#141414" stroke-width="1"/></svg>
          simon@harcourtmemorials.com.au
        </p>
      </div>
      <div class="person">
        <p class="person__name">Lewis Harcourt</p>
        <p class="person__role">Director</p>
        <p class="person__line">
          <svg class="icon" viewBox="0 0 12 12"><path fill="#f2b705" d="M2.4 1l2 2.2-1 1.2c.7 1.5 1.8 2.6 3.3 3.3l1.2-1 2.1 2-1.1 1.8C5.4 10.2 1.8 6.6 1 3l1.4-2z"/></svg>
          0491630572
        </p>
        <p class="person__line">
          <svg class="icon" viewBox="0 0 12 12"><rect x="1" y="2.5" width="10" height="7" fill="#f2b705"/><path d="M1 2.5l5 4 5-4" fill="none" stroke="#141414" stroke-width="1"/></svg>
          lewis@harcourtmemorials.com.au
        </p>
      </div>
    </div>
  </section>

  <section class="card card--back">
    <div class="brand">
      <span class="brand__mark"></span>
      <span class="brand__name">Harcourt<br>Memorials</span>
    </div>
    <div class="company-info">
      <p><span class="label">P:</span> 02 9561 3048<span class="sep">|</span><span class="web">www.harcourtmemorials.com.au</span></p>
      <p>Suite 17, 8 Palfrey Lane, West Carlow, Sydney NSW 2156</p>
    </div>
  </section>
</main>
</body>
</html>
```